Larkspur Talent IT Recruiting firm needs a business card design for Recruiters, Sourcers, and Account

We need business cards that allow us to change all contact info, names, titles (Recruiter, Sourcer, Account Manager, Director, CEO, etc) per person since we have three offices, in three cities, Phoenix, Austin, and Las Vegas. We do recruiting and contractors for IT positions (Developers, Architects, Software Engineers, Security Engineers, Help Desk, DBAs, PMs, Scrum Masters, etc.) Our client companies are very diverse from Meridian 100 to silicone Valley type start-ups.

So, while we what hip, techie, and quirky, it still needs to be professional. Primary color we use is blue, with silver as a secondary color.

Target Market(s)

IT, Technology

Industry/Entity Type

Business

Contact Information for Business Card

Company name: Larkspur Talent, Inc.
Website: www.larkspurtalent.example
Logos for Careerloop, Blipster, and Myriada

Name, Title, Office Number, Cell Number, email

Font styles to use
Serif
Sans Serif

Colors
0455a3
d5d5d5

Requirements
Nice to have
• The grey I selected below is not necessary - but, would like silver included. I included a card design (File 3: LTI early trial example.jpg) that I had started on. It's very rough, and not quite what we're looking for, but what we did like is the logo, big, maybe a bit faded, off center, goes out of frame, etc. Still looking for other ideas - you are the pros! But, just an idea of a design element we liked.

```html
<!DOCTYPE html>
<html lang="en">
<head>
<meta charset="utf-8">
<title>Larkspur Talent — Business Card</title>
<link rel="stylesheet" href="https://fonts.googleapis.com/css2?family=Lora:wght@600&family=Montserrat:wght@500;700&display=swap">
<style>
  :root {
    --brand-blue: #0b55a3;
    --silver-dark: #929396;
    --silver-mid: #b4b5b8;
    --silver-light: #e6e7e8;
    --ink-light: #ffffff;
  }
  html, body {
    margin: 0;
    padding: 0;
    width: 1200px;
    height: 720px;
    overflow: hidden;
    background: var(--brand-blue);
  }
  .card {
    position: relative;
    width: 1200px;
    height: 720px;
    background: var(--brand-blue);
    overflow: hidden;
  }
  .emblem {
    position: absolute;
    left: 0;
    top: 0;
    width: 1200px;
    height: 720px;
  }
  .emblem-name {
    font-family: "Montserrat", Arial, sans-serif;
    font-weight: 700;
    font-size: 72px;
    letter-spacing: 2px;
    fill: var(--brand-blue);
  }
  .contact {
    position: absolute;
    left: 962px;
    top: 64px;
    width: 222px;
    bottom: 56px;
    display: flex;
    flex-direction: column;
    color: var(--ink-light);
    font-family: "Montserrat", Arial, sans-serif;
    font-weight: 500;
  }
  .person-name {
    margin: 0;
    font-family: "Lora", Georgia, serif;
    font-weight: 600;
    font-size: 28px;
    line-height: 1.15;
  }
  .person-title {
    margin: 8px 0 0;
    font-size: 14px;
    letter-spacing: 1px;
    text-transform: uppercase;
    color: var(--silver-light);
  }
  .rule {
    width: 48px;
    height: 2px;
    margin: 26px 0;
    background: var(--silver-mid);
    border: 0;
  }
  .details {
    margin: 0;
    padding: 0;
    list-style: none;
    font-size: 13px;
    line-height: 2;
  }
  .details .label {
    display: inline-block;
    width: 52px;
    color: var(--silver-mid);
  }
  .email { font-size: 12px; }
  .company {
    margin: auto 0 0;
    font-size: 15px;
    font-weight: 700;
  }
  .website {
    margin: 4px 0 0;
    font-size: 13px;
    color: var(--silver-light);
  }
  .offices {
    margin: 14px 0 0;
    font-size: 12px;
    color: var(--silver-mid);
  }
  .social {
    display: flex;
    gap: 14px;
    margin: 18px 0 0;
    padding: 0;
    list-style: none;
    font-size: 12px;
  }
  .social li {
    display: flex;
    align-items: center;
    gap: 5px;
  }
  .social li::before {
    content: "";
    width: 8px;
    height: 8px;
    background: var(--silver-mid);
  }
</style>
</head>
<body>
  <main class="card">
    <svg class="emblem" viewBox="0 0 1200 720" role="img" aria-label="Larkspur Talent emblem, large and cropped at the card edge">
      <defs>
        <linearGradient id="silver-sheen" x1="0" y1="0" x2="0" y2="720" gradientUnits="userSpaceOnUse">
          <stop offset="0" style="stop-color: var(--silver-dark)"/>
          <stop offset="0.38" style="stop-color: var(--silver-dark)"/>
          <stop offset="0.67" style="stop-color: var(--silver-light)"/>
          <stop offset="0.88" style="stop-color: var(--silver-mid)"/>
          <stop offset="1" style="stop-color: var(--silver-dark)"/>
        </linearGradient>
      </defs>
      <circle class="emblem-disc" cx="470" cy="380" r="470" fill="url(#silver-sheen)"/>
      <text class="emblem-name" x="470" y="405" text-anchor="middle">Larkspur Talent</text>
    </svg>

    <section class="contact">
      <h1 class="person-name">Jordan Ellery</h1>
      <p class="person-title">Senior IT Recruiter</p>
      <hr class="rule">
      <ul class="details">
        <li><span class="label">Office</span>(602) 555-0148</li>
        <li><span class="label">Cell</span>(602) 555-0193</li>
        <li class="email">j.ellery@larkspurtalent.example</li>
      </ul>
      <p class="company">Larkspur Talent, Inc.</p>
      <p class="website">www.larkspurtalent.example</p>
      <p class="offices">Phoenix · Austin · Las Vegas</p>
      <ul class="social">
        <li>Careerloop</li>
        <li>Blipster</li>
        <li>Myriada</li>
      </ul>
    </section>
  </main>
</body>
</html>
```